Kestrelbrook Student Accomodation needs a business card design

Hi Guys,

We are a Student Accommodation company in Australia. We already have a logo which I will submit.

I will require the design of the business cards from you.

I am after something that looks clean, modern and that people feel interested and actually want to contact us.

We would like to see designs that are innovative.

On the business cards I will require to have:

Employee Name
Position
Phone number
Email
Facebook page

I hope you can help me with this project guys as I have heard really good things from you.

```html
<!DOCTYPE html>
<html lang="en">
<head>
<meta charset="utf-8">
<title>Kestrelbrook Student Accomodation – Business Card</title>
<link rel="stylesheet" href="https://fonts.googleapis.com/css2?family=Noto+Sans:wght@400;600&display=swap">
<style>
  :root {
    --green: #0f8a2c;
    --green-dark: #0b6e22;
    --yellow: #f0b431;
    --ink: #1d1d1d;
    --paper: #ffffff;
    --backdrop: #e6e6e6;
  }
  * { box-sizing: border-box; margin: 0; padding: 0; }
  html, body { width: 1200px; height: 680px; overflow: hidden; }
  body {
    background: var(--backdrop);
    font-family: "Noto Sans", Verdana, sans-serif;
    color: var(--ink);
    position: relative;
  }
  .card {
    position: absolute;
    top: 185px;
    width: 540px;
    height: 310px;
    background: var(--paper);
    box-shadow: 0 6px 18px rgba(0,0,0,0.18);
    overflow: hidden;
  }
  .card--front { left: 45px; }
  .card--back { left: 615px; }

  .brand {
    display: flex;
    align-items: center;
    gap: 14px;
  }
  .brand__mark { background: var(--yellow); flex: none; }
  .brand__name {
    color: var(--green);
    font-weight: 600;
    line-height: 1.1;
  }

  /* front */
  .card--front .brand {
    position: absolute;
    left: 0; right: 0; top: 80px;
    justify-content: center;
  }
  .card--front .brand__mark { width: 70px; height: 70px; }
  .card--front .brand__name { font-size: 26px; }
  .front-band {
    position: absolute;
    left: 0; right: 0; bottom: 0;
    height: 42px;
    background: var(--green);
    color: var(--paper);
    font-size: 15px;
    letter-spacing: 2px;
    text-align: right;
    padding: 10px 26px 0 0;
  }

  /* back */
  .back-art { position: absolute; inset: 0; }
  .card--back .brand { position: absolute; left: 32px; top: 100px; gap: 10px; }
  .card--back .brand__mark { width: 42px; height: 42px; }
  .card--back .brand__name { font-size: 16px; }
  .person {
    position: absolute;
    left: 32px; top: 198px;
    display: flex; align-items: baseline; gap: 8px;
  }
  .person__name { color: var(--green); font-size: 19px; }
  .person__role { font-size: 13px; }
  .contact {
    position: absolute;
    display: flex; align-items: center; gap: 7px;
    font-size: 13px;
    white-space: nowrap;
  }
  .contact svg { width: 14px; height: 14px; flex: none; }
  .contact--phone { left: 32px; top: 252px; font-size: 15px; letter-spacing: 0.5px; }
  .contact--email { left: 320px; top: 150px; }
  .contact--social { left: 320px; top: 170px; }
</style>
</head>
<body>

<section class="card card--front" aria-label="Card front">
  <div class="brand">
    <span class="brand__mark"></span>
    <span class="brand__name">Kestrelbrook<br>Student Accomodation</span>
  </div>
  <div class="front-band">friendspace.net/kestrelbrook</div>
</section>

<section class="card card--back" aria-label="Card back">
  <svg class="back-art" viewBox="0 0 540 310" aria-hidden="true">
    <polygon points="0,22 168,22 160,34 0,34" fill="var(--green)"/>
    <polygon points="190,0 540,0 540,9 183,9" fill="var(--yellow)"/>
    <line x1="200" y1="86" x2="540" y2="86" stroke="var(--green-dark)" stroke-width="1.5"/>
    <line x1="28" y1="188" x2="300" y2="188" stroke="var(--green-dark)" stroke-width="1.5"/>
    <polygon points="0,290 385,290 370,310 0,310" fill="var(--yellow)"/>
    <polygon points="395,280 540,280 540,310 380,310" fill="var(--green)"/>
  </svg>

  <div class="brand">
    <span class="brand__mark"></span>
    <span class="brand__name">Kestrelbrook<br>Student Accomodation</span>
  </div>

  <div class="person">
    <span class="person__name">Marcus Ellery</span>
    <span class="person__role">manager</span>
  </div>

  <div class="contact contact--email">
    <svg viewBox="0 0 16 16" aria-hidden="true"><rect x="1" y="3" width="14" height="10" fill="var(--green)"/><polyline points="1,3 8,9 15,3" fill="none" stroke="#fff" stroke-width="1.3"/></svg>
    <span>info@kestrelbrook.com</span>
  </div>
  <div class="contact contact--social">
    <svg viewBox="0 0 16 16" aria-hidden="true"><circle cx="8" cy="4.5" r="3" fill="var(--green)"/><path d="M2 15 Q2 8.5 8 8.5 Q14 8.5 14 15 Z" fill="var(--green)"/></svg>
    <span>friendspace.net/kestrelbrook</span>
  </div>
  <div class="contact contact--phone">
    <svg viewBox="0 0 16 16" aria-hidden="true"><path d="M4 1.5 L6.5 4.5 L5 6.5 Q6.5 9.5 9.5 11 L11.5 9.5 L14.5 12 L12.5 14.5 Q6 14 1.5 3.5 Z" fill="var(--green)"/></svg>
    <span>040 555 0172</span>
  </div>
</section>

</body>
</html>
```